Brindlewick Solutions Ltd

I'd like to create a company letterhead for the attached logo in word format.

I'd like to emphasis the icon in large translucent state from the left corner and ensure that the letterhead colouring matches the colour palette of the current logo with a contrast so it's clear to see. I've attached a copy of our sister company page on the app for reference.

```html
<!DOCTYPE html>
<html lang="en">
<head>
<meta charset="utf-8">
<title>Brindlewick Solutions Ltd — Letterhead</title>
<link href="https://fonts.googleapis.com/css2?family=Arimo:wght@400&family=Montserrat:wght@400;700&family=Hind:wght@300&display=swap" rel="stylesheet">
<style>
  :root {
    --teal: #14bca7;
    --rule-grey: #9a9a9a;
    --ink: #555555;
    --ink-soft: #8a8a8a;
    --paper: #ffffff;
    --backdrop: #e2e2e2;
  }
  * { margin: 0; padding: 0; box-sizing: border-box; }
  html, body { width: 1200px; height: 1200px; overflow: hidden; background: var(--backdrop); }
  .sheet {
    position: absolute; left: 233px; top: 81px; width: 734px; height: 1038px;
    background: var(--paper);
  }
  .band { position: absolute; background: var(--teal); height: 6px; top: 104px; }
  .band--left { left: 0; width: 62px; }
  .band--right { left: 315px; right: 0; }
  .rule { position: absolute; background: var(--rule-grey); height: 2px; top: 117px; }
  .rule--left { left: 0; width: 67px; }
  .rule--right { left: 132px; right: 0; }
  .brand { position: absolute; left: 66px; top: 58px; display: flex; align-items: center; }
  .brand__dot { width: 44px; height: 44px; border-radius: 50%; background: var(--teal); margin-right: 12px; }
  .brand__name {
    font-family: "Montserrat", sans-serif; font-weight: 400; color: var(--teal);
    font-size: 27px; line-height: 1; letter-spacing: -0.5px;
  }
  .brand__name small {
    display: block; font-size: 8.5px; letter-spacing: 6.2px; margin-top: 6px;
  }
  .contact { position: absolute; top: 45px; font-family: "Arimo", sans-serif; font-size: 11px; line-height: 17px; color: var(--ink-soft); }
  .contact--address { right: 219px; text-align: right; }
  .contact__divider { position: absolute; left: 527px; top: 50px; width: 1px; height: 42px; background: var(--rule-grey); }
  .contact--channels { left: 538px; }
  .contact--channels li { list-style: none; display: flex; align-items: center; gap: 6px; }
  .contact--channels svg { width: 10px; height: 10px; }
  .letter { position: absolute; left: 66px; top: 318px; width: 600px; color: var(--ink); }
  .letter__greeting { font-family: "Montserrat", sans-serif; font-weight: 700; font-size: 16px; margin-left: 2px; margin-bottom: 27px; }
  .letter__body p { font-family: "Arimo", sans-serif; font-size: 12.1px; line-height: 15px; margin-bottom: 13px; text-align: justify; }
  .letter__closing { font-family: "Montserrat", sans-serif; font-weight: 700; font-size: 9.5px; margin: 26px 0 0 2px; }
  .letter__signature { font-family: "Hind", sans-serif; font-weight: 300; font-size: 19px; letter-spacing: -1px; margin: 34px 0 0 19px; color: #4a4a4a; }
</style>
</head>
<body>
<main class="sheet">
  <header class="letterhead">
    <div class="band band--left"></div>
    <div class="band band--right"></div>
    <div class="rule rule--left"></div>
    <div class="rule rule--right"></div>
    <div class="brand">
      <span class="brand__dot"></span>
      <span class="brand__name">Brindlewick<small>SOLUTIONS LTD</small></span>
    </div>
    <address class="contact contact--address" style="font-style:normal">Your address<br>city<br>state, ZIP 0000</address>
    <div class="contact__divider"></div>
    <ul class="contact contact--channels">
      <li><svg viewBox="0 0 10 10"><path d="M2 1 L4 3 L3 4 Q4 6 6 7 L7 6 L9 8 L8 9 Q4 9 1 5 Q1 2 2 1Z" fill="var(--teal)"/></svg>123-456-2100</li>
      <li><svg viewBox="0 0 10 10"><rect x="0.5" y="2" width="9" height="6" fill="var(--teal)"/><path d="M0.5 2 L5 5.5 L9.5 2" stroke="#fff" stroke-width="0.8" fill="none"/></svg>youremail@mailhost.com</li>
      <li><svg viewBox="0 0 10 10"><circle cx="5" cy="5" r="4.5" fill="var(--teal)"/><path d="M0.5 5 H9.5 M5 0.5 Q2.5 5 5 9.5 M5 0.5 Q7.5 5 5 9.5" stroke="#fff" stroke-width="0.7" fill="none"/></svg>www.yourwebsite.com</li>
    </ul>
  </header>
  <article class="letter">
    <h1 class="letter__greeting">Dear Mr. Hallam,</h1>
    <div class="letter__body">
      <p>Lorem ipsum dolor sit amet, consectetuer adipiscing elit, sed diam nonmmy nibh euismod tincidunt ut laor eet dolore magna aliquam erat volutpat. Ut wisi enim ad minim veniam, quis nostrud exerci tationmcorper suscipit lobortis nisl ut aliquip ex ea commodo consequat. Duis autem vel eum iriure dolor in hendrerit in vulputate velit esse molestie consequat, vel illum dolore eu feugiat</p>
      <p>Rorem ipsum dolor sit amet, consectetuer adipiscing elit, sed diam nonmmy nibh euismod tincidunt ut laor eet dolore magna aliquam erat volutpat. Ut wisi enim ad minim veniam, quis nostrud exerci tationmcorper suscipit lobortis nisl ut aliquip ex ea commodo consequat. Duis autem vel eum iriure dolor in hendrerit in vulputate velit esse molest</p>
      <p>Dorem ipsum dolor sit amet, consectetuer adipiscing elit, sed diam nonmmy nibh euismod tincidunt ut laor eet dolore magna aliquam erat volutpat. Ut wisi enim ad minim veniam, quis nostrud exerci tationmcorper suscipit lobortis nisl ut aliquip ex ea commodo consequat. Duis autem vel eum iriure dolor in hendrerit in suscipit lobortis nisl ut aliquip ex ea commodo consequat. Duis autem vel eum iriure dolor in hendrerit in vulputate velit esse molestie consequat, vel illum</p>
      <p>Sorem ipsum dolor sit amet, consectetuer adipiscing elit, sed diam nonmmy nibh euismod tincidunt ut laor eet dolore magna aliquam erat volutpat. Ut wisi enim ad minim veniam, quis nostrud exerci tationmcorper suscipit lobortis nisl ut aliquip ex ea commodo consequat. Duis autem vel eum iriure dolor in</p>
    </div>
    <p class="letter__closing">Sincerely,</p>
    <p class="letter__signature">Marten Ellsworth</p>
  </article>
</main>
</body>
</html>
```